Help our Sugar Loom find our winning design! We're looking for a business card....

We’re a Sugar Loom in NY specializing in custom-made cakes and unique desserts.
Our cakes combine flavor and art, each designed to match customer’s special event and theme.
We’d like a unique business card with a clean design that will combine French chic and artistic look & feel.
We’d like to differentiate ourselves from standard bakeries, please don’t offer cupcake images :-)
Our logo is peach-pink and brown and we’d love to use these colors ( . Another color that can be added is gold - or feel free to suggest!

Target Market(s)

Women, ages 25-55

Industry/Entity Type

Boutique

Contact Information for Business Card

Text on card:
Logo
Sugar Loom by Dana Welch

www.sugarloomsweets.com
hello@sugarloom.com
(516) 555-0147
F – sugarloomnyc
IG - sugarloom_ny

Font styles to use
Sans Serif
Script

Requirements
Must have
• Logo
• Clean look
• French chic and artistic look & feel.
Nice to have
• Damask pattern
Should not have
• Cupcake images

```html
<!DOCTYPE html>
<html lang="en">
<head>
<meta charset="utf-8">
<title>Sugar Loom – Business Card</title>
<link rel="stylesheet" href="https://fonts.googleapis.com/css2?family=Open+Sans:wght@400;600&family=Pinyon+Script&display=swap">
<style>
  :root {
    --backdrop: #b9b9b9;
    --card: #ffffff;
    --blush: #e0a79d;
    --blush-soft: #f1d3cd;
    --cocoa: #3b2f2f;
    --ink: #2e2a2a;
  }
  * { box-sizing: border-box; margin: 0; padding: 0; }
  html, body {
    width: 1200px; height: 852px; overflow: hidden;
    background: var(--backdrop);
    font-family: "Open Sans", Arial, sans-serif;
    color: var(--ink);
  }
  .stage {
    position: relative; width: 1200px; height: 852px;
    display: flex; align-items: center; justify-content: center; gap: 60px;
  }
  .card {
    position: relative;
    width: 520px; height: 300px;
    background: var(--card);
    border-radius: 26px;
    box-shadow: 0 6px 14px rgba(0,0,0,.25);
    overflow: hidden;
  }
  .brand {
    position: absolute;
    display: flex; align-items: center; gap: 10px;
    font-family: "Open Sans", Arial, sans-serif;
    font-weight: 400;
    color: var(--cocoa);
    white-space: nowrap;
  }
  .brand-dot {
    display: block; border-radius: 50%; background: var(--blush);
  }
  .card-front .brand {
    left: 50%; top: 50%; transform: translate(-50%, -50%);
    font-size: 46px; letter-spacing: 1px;
  }
  .card-front .brand-dot { width: 16px; height: 16px; }
  .card-back .brand {
    left: 130px; top: 150px; transform: translate(-50%, -50%);
    font-size: 28px;
  }
  .card-back .brand-dot { width: 11px; height: 11px; }
  .divider {
    position: absolute; left: 262px; top: 40px; width: 1px; height: 220px;
    background: linear-gradient(var(--blush-soft), var(--blush), var(--blush-soft));
  }
  .owner {
    position: absolute; left: 292px; top: 50px;
  }
  .owner-line { font-size: 15px; color: var(--ink); }
  .owner-name {
    font-family: "Pinyon Script", cursive;
    font-size: 34px; line-height: 1.2; color: var(--cocoa);
  }
  .contacts {
    position: absolute; left: 292px; top: 150px;
    list-style: none; font-size: 12.5px; line-height: 19px;
  }
  .contacts li { display: flex; align-items: center; gap: 9px; }
  .contacts svg { width: 11px; height: 11px; flex: none; }
  .mark-square { width: 9px; height: 9px; background: var(--blush); border-radius: 2px; margin: 0 1px; flex: none; }
</style>
</head>
<body>
<main class="stage">
  <section class="card card-front">
    <div class="brand"><span class="brand-dot"></span>Sugar Loom</div>
  </section>

  <section class="card card-back">
    <div class="brand"><span class="brand-dot"></span>Sugar Loom</div>
    <div class="divider"></div>
    <div class="owner">
      <p class="owner-line">Sugar Loom by</p>
      <p class="owner-name">Dana Welch</p>
    </div>
    <ul class="contacts">
      <li>
        <svg viewBox="0 0 12 12"><path fill="var(--blush)" d="M2 1h3l1 3-1.5 1a6 6 0 0 0 2.5 2.5L8 6l3 1v3a1 1 0 0 1-1 1A9 9 0 0 1 1 2a1 1 0 0 1 1-1z"/></svg>
        (516) 555-0147
      </li>
      <li>
        <svg viewBox="0 0 12 12"><rect x="0.5" y="2" width="11" height="8" rx="1" fill="var(--blush)"/><path d="M1 2.6l5 4 5-4" stroke="#fff" stroke-width="1" fill="none"/></svg>
        hello@sugarloom.com
      </li>
      <li>
        <svg viewBox="0 0 12 12"><circle cx="6" cy="6" r="5" fill="none" stroke="var(--blush)" stroke-width="1.3"/><path d="M1 6h10M6 1c-2 3-2 7 0 10M6 1c2 3 2 7 0 10" stroke="var(--blush)" stroke-width="1" fill="none"/></svg>
        www.sugarloomsweets.com
      </li>
      <li><span class="mark-square"></span>sugarloomnyc</li>
      <li><span class="mark-square"></span>sugarloom_ny</li>
    </ul>
  </section>
</main>
</body>
</html>
```